I am looking for a design for my superfood powder. It is a meal replacement powder that is raw and organic. It contains items such as camu , maca, bee pollen, spinach , nettles, and other leafy greens and antioxidant berries. The jar is round , 3 1/2 inches in diameter . The label will wrap all the way around with ingredients on the back. Go to wwwk2rbloomtrail.com and look at the on line store. you will find a better description there. I have a logo that the design needs to work with . You can also find the logo on the website. This needs to be a very unique design. This product will be sold to stores and individuals nation wide.

Graphic Design

• 1 Idea /some kind of natural raw arrangement of the above products on natural raw paper.
2nd idea use creativity to protray products. Symbols ect
Logo must be in project.
Asmall space for product description and name

```html
<!DOCTYPE html>
<html lang="en">
<head>
<meta charset="utf-8">
<title>bloomtrail Superfood Weight Loss Powder – Jar Label</title>
<link rel="stylesheet" href="https://fonts.googleapis.com/css2?family=Arimo:wght@400;700&family=Tinos:wght@700&display=swap">
<style>
  :root {
    --kraft-light: #d9a672;
    --kraft-mid: #c98f58;
    --kraft-dark: #b57a45;
    --rule-white: #fbf7f0;
    --band-green: #5f7a32;
    --band-warm: #a85a34;
    --band-gold: #d8b43a;
    --panel-fill: rgba(128, 134, 48, 0.92);
    --panel-border: #4aa51b;
    --text-white: #ffffff;
    --logo-grey: #4b4b4b;
  }
  * { margin: 0; padding: 0; box-sizing: border-box; }
  html, body {
    width: 1200px;
    height: 654px;
    overflow: hidden;
    background: #ffffff;
  }
  .label {
    position: relative;
    width: 1200px;
    height: 654px;
    overflow: hidden;
    font-family: "Arimo", Arial, sans-serif;
    color: var(--text-white);
  }
  .kraft-paper {
    position: absolute;
    inset: 0;
    background:
      radial-gradient(ellipse at 50% 50%, var(--kraft-light) 0%, var(--kraft-mid) 60%, var(--kraft-dark) 100%);
  }
  .brand {
    position: absolute;
    top: 96px;
    left: 0;
    width: 1200px;
    display: flex;
    justify-content: center;
    align-items: center;
    gap: 12px;
    font-family: "Arimo", Arial, sans-serif;
    font-weight: 700;
    font-size: 44px;
    letter-spacing: -0.5px;
    color: var(--logo-grey);
  }
  .brand-dot {
    width: 30px;
    height: 30px;
    border-radius: 50%;
    background: var(--logo-grey);
  }
  .rule {
    position: absolute;
    left: 0;
    width: 1200px;
    height: 3px;
    background: var(--rule-white);
  }
  .rule-top { top: 168px; }
  .rule-bottom { top: 541px; }
  .produce-band {
    position: absolute;
    top: 172px;
    left: 0;
    width: 1200px;
    height: 368px;
    background:
      radial-gradient(ellipse 320px 220px at 590px 170px, rgba(230, 200, 60, 0.85), rgba(230, 200, 60, 0) 70%),
      radial-gradient(ellipse 260px 200px at 110px 110px, rgba(170, 70, 50, 0.8), rgba(170, 70, 50, 0) 75%),
      radial-gradient(ellipse 260px 200px at 1110px 90px, rgba(160, 60, 40, 0.7), rgba(160, 60, 40, 0) 75%),
      radial-gradient(ellipse 200px 160px at 720px 150px, rgba(130, 70, 40, 0.8), rgba(130, 70, 40, 0) 75%),
      linear-gradient(180deg, #6d7f38 0%, var(--band-green) 55%, #486326 100%);
  }
  .panel {
    position: absolute;
    top: 249px;
    width: 300px;
    height: 238px;
    background: var(--panel-fill);
    border: 5px solid var(--panel-border);
    border-radius: 6px;
    font-weight: 700;
    text-align: center;
  }
  .panel-summary {
    left: 81px;
    padding: 32px 16px 0;
    font-size: 17px;
    line-height: 21px;
  }
  .panel-summary p + p { margin-top: 22px; }
  .panel-ingredients {
    left: 820px;
    padding-top: 12px;
    font-size: 26px;
  }
  .product-title {
    position: absolute;
    top: 192px;
    left: 352px;
    width: 500px;
    text-align: center;
    font-family: "Tinos", "Times New Roman", serif;
    font-weight: 700;
    text-shadow: 1px 2px 3px rgba(0, 0, 0, 0.45);
  }
  .product-title .title-main {
    display: block;
    font-size: 44px;
    line-height: 46px;
    letter-spacing: 1px;
  }
  .product-title .title-sub {
    display: block;
    font-size: 23px;
    line-height: 26px;
  }
  .tagline {
    position: absolute;
    top: 304px;
    left: 352px;
    width: 500px;
    text-align: center;
    font-weight: 700;
    text-shadow: 1px 1px 3px rgba(0, 0, 0, 0.45);
  }
  .tagline .tag-main { display: block; font-size: 26px; line-height: 30px; }
  .tagline .tag-sub { display: block; font-size: 21px; line-height: 28px; }
  .contents {
    position: absolute;
    top: 424px;
    left: 452px;
    width: 320px;
    text-align: center;
    font-weight: 700;
    font-size: 16.5px;
    line-height: 21px;
    text-shadow: 1px 1px 3px rgba(0, 0, 0, 0.6);
  }
</style>
</head>
<body>
  <main class="label">
    <div class="kraft-paper" role="img" aria-label="Natural raw kraft paper texture"></div>

    <div class="brand">
      <span class="brand-name">bloomtrail</span>
      <span class="brand-dot" aria-hidden="true"></span>
    </div>

    <div class="rule rule-top"></div>
    <div class="produce-band" role="img" aria-label="Natural arrangement of pomegranate, powdered greens, persimmon, blueberries, cinnamon sticks, leafy greens, nettles, rose hips and wildflowers"></div>
    <div class="rule rule-bottom"></div>

    <section class="panel panel-summary">
      <p>100% Whole-Food Meal Replacement Powder with Protein, Vitamins, Minerals and Antioxidants</p>
      <p>Contains over 20 Fruits, Vegetables, and Herbs</p>
    </section>

    <h1 class="product-title">
      <span class="title-main">SUPERFOOD</span>
      <span class="title-sub">WEIGHT LOSS POWDER</span>
    </h1>

    <p class="tagline">
      <span class="tag-main">Integrating Healthy</span>
      <span class="tag-sub">Weight Loss and Nutrition</span>
    </p>

    <p class="contents">Contains items such as camu , maca, bee pollen, spinach , nettles, and other leafy greens and antioxidant berries.</p>

    <section class="panel panel-ingredients">
      <h2 class="ingredients-heading">Ingredients:</h2>
    </section>
  </main>
</body>
</html>
```